Request for Business Card Design

Hi. My name is Marlene, I am looking for a new business card design for my company, Quarrow Signal Instruments, LLC. I really like the design you did for Tarsel Venture and was hoping you could do something similar using our full logo and our mark. I am also open to any raised texture design using our mark. I have attached our full logo, which would need to be somewhere on the card, as well as the mark in both outline and full form, as well as our brand colors / guide. The card does not have to be white, as long as our logo and mark appear. I actually like darker colored business cards more, but am open to all options. If you are interested in working with me, please let me know. We would also take the business card design into letterhead design if you can do that.

```html
<!DOCTYPE html>
<html lang="en">
<head>
<meta charset="utf-8">
<title>Quarrow Signal Instruments — Business Card</title>
<link rel="stylesheet" href="https://fonts.googleapis.com/css2?family=Exo+2:wght@700&family=Arimo:wght@400;700&display=swap">
<style>
  :root {
    --backdrop: #0d0d0d;
    --card: #232323;
    --card-deep: #1b1b1b;
    --accent: #0b8db5;
    --ink: #f2f2f2;
    --ink-soft: #d9d9d9;
    --raised: #2c2c2c;
  }
  * { margin: 0; padding: 0; box-sizing: border-box; }
  html, body { width: 1200px; height: 963px; overflow: hidden; background: var(--backdrop); }
  .sheet { position: relative; width: 1200px; height: 963px; }
  .card {
    position: absolute; left: 220px; width: 760px; height: 434px;
    background: var(--card); border-radius: 26px;
    border-bottom: 4px solid var(--accent);
    overflow: hidden;
  }
  .card--front { top: 36px; }
  .card--back { top: 497px; }

  .wordmark { position: absolute; display: flex; align-items: center; gap: 18px; }
  .wordmark__dot { width: 56px; height: 56px; border-radius: 50%; background: var(--accent); flex: none; }
  .wordmark__text { font-family: "Exo 2", sans-serif; font-weight: 700; color: var(--ink); line-height: 1; }
  .wordmark__name { display: block; letter-spacing: 0.08em; }
  .wordmark__sub { display: block; letter-spacing: 0.05em; margin-top: 6px; }

  .card--front .wordmark { left: 56px; top: 140px; }
  .card--front .wordmark__name { font-size: 44px; }
  .card--front .wordmark__sub { font-size: 15px; }

  .divider { position: absolute; left: 392px; top: 120px; width: 1px; height: 200px; background: var(--ink-soft); transform: rotate(18deg); }

  .contact { position: absolute; left: 440px; top: 110px; font-family: "Arimo", sans-serif; color: var(--ink); }
  .contact__name { font-weight: 700; font-size: 24px; color: var(--accent); letter-spacing: 0.04em; }
  .contact__role { font-size: 17px; margin-top: 4px; }
  .contact__address { font-size: 17px; margin-top: 22px; line-height: 1.35; }
  .contact__list { list-style: none; margin-top: 22px; }
  .contact__item { display: flex; align-items: center; gap: 12px; font-size: 17px; margin-bottom: 9px; }
  .contact__item svg { width: 16px; height: 16px; flex: none; }

  .card--back .wordmark { left: 64px; top: 150px; }
  .card--back .wordmark__name { font-size: 64px; }
  .card--back .wordmark__sub { font-size: 21px; margin-top: 8px; }
  .raised-disc {
    position: absolute; right: -40px; top: 60px; width: 360px; height: 360px; border-radius: 50%;
    background: radial-gradient(circle at 40% 35%, var(--raised), var(--card-deep));
    box-shadow: inset 6px 8px 14px rgba(255,255,255,0.05), inset -8px -10px 18px rgba(0,0,0,0.55);
  }
</style>
</head>
<body>
<main class="sheet">
  <section class="card card--front" aria-label="Card front">
    <div class="wordmark">
      <span class="wordmark__dot"></span>
      <span class="wordmark__text">
        <span class="wordmark__name">QUARROW</span>
        <span class="wordmark__sub">SIGNAL INSTRUMENTS</span>
      </span>
    </div>
    <span class="divider"></span>
    <div class="contact">
      <p class="contact__name">JONAH PELLWARD</p>
      <p class="contact__role">Manager</p>
      <p class="contact__address">48 Harlow Lane, Brenton<br>OH, 43210</p>
      <ul class="contact__list">
        <li class="contact__item">
          <svg viewBox="0 0 16 16" aria-hidden="true"><path d="M4 1.5l2.2 3-1.4 1.6a8 8 0 0 0 5.1 5.1l1.6-1.4 3 2.2-1.3 2.4C7.5 14.6 1.4 8.5 1.6 2.8z" fill="var(--accent)"/></svg>
          555-014-2736
        </li>
        <li class="contact__item">
          <svg viewBox="0 0 16 16" aria-hidden="true"><rect x="1.5" y="3.5" width="13" height="9" rx="1" fill="none" stroke="var(--accent)" stroke-width="1.4"/><path d="M1.5 4l6.5 5 6.5-5" fill="none" stroke="var(--accent)" stroke-width="1.4"/></svg>
          jonah@quarrowsignal.com
        </li>
        <li class="contact__item">
          <svg viewBox="0 0 16 16" aria-hidden="true"><circle cx="8" cy="8" r="6.5" fill="none" stroke="var(--accent)" stroke-width="1.3"/><ellipse cx="8" cy="8" rx="2.8" ry="6.5" fill="none" stroke="var(--accent)" stroke-width="1.1"/><path d="M1.5 8h13M2.5 5h11M2.5 11h11" stroke="var(--accent)" stroke-width="1.1"/></svg>
          www.quarrowsignal.com
        </li>
      </ul>
    </div>
  </section>

  <section class="card card--back" aria-label="Card back">
    <span class="raised-disc"></span>
    <div class="wordmark">
      <span class="wordmark__text">
        <span class="wordmark__name">QUARROW</span>
        <span class="wordmark__sub">SIGNAL INSTRUMENTS</span>
      </span>
    </div>
  </section>
</main>
</body>
</html>
```